Mobile app for checking bus arrival

I would like to make the UI much more beautiful and modern. The app is an app to check bus arrival in Singapore.
See here: https://apps.veltrano.com/store/apps/details?id=com.ridoka&hl=en

Based on the question from designers:

1. The first screen shows the favorite bus stop. Each item shows location / street, the top one is the location, second line is the street name. And the number is the bus stop code.

2. Please download the app and try bus stop code with 07589 or 10079, for example. It will bring you to the next screen.

3. The pencil allow you to select color theme, for the list item, and the header.

4. On the second screen, it will show up the list of bus route that available on that bus stop.

5. When you tap on one of them it will show you the 2 subsequent arrival time.

6. Each of the arrival time has the information of availability seats available, seats not available, no more space. (we can use green, yellow, red, respectively).

7. Each of the arrival time has the WAB indicator (Wheelchair availability). Show as icon is preferred.

7. KLT and VOPN are the bus provider in Singapore. 48 means the route /service no.

Requirements:
And check the attachment, see screen 3. I need to add information about the space availability, which has 3 state: seats available, seats not available, no more space. (we can use green, yellow, red, respectively).

Please advise how to show the information.

Target Market(s)

Students, age below 35

Industry/Entity Type

Trivex

Requirements
Must have
• The app currently has the capabilities to select color theme, checkout screen1. It's the button and the list item color.
Nice to have
• Please download the app to see all available colors, and make suggestion to have better color pallete.

```html
<!DOCTYPE html>
<html lang="en">
<head>
<meta charset="utf-8">
<title>Bus Stop Favourites</title>
<link href="https://fonts.googleapis.com/css2?family=Open+Sans:ital,wght@0,400;0,600;1,400&display=swap" rel="stylesheet">
<style>
:root{
  --header-blue:#5b84ef;
  --field-blue:#4a69c9;
  --item-blue:#5a82f2;
  --code-blue:#6b91f5;
  --go-green:#3cbf2a;
  --white:#ffffff;
  --star:#f7bd1c;
  --check-green:#2fb52a;
  --ad-dark:#2b2b2b;
  --ad-gold:#b97a1e;
}
html,body{margin:0;padding:0;width:676px;height:1200px;overflow:hidden;background:var(--white);}
.screen{position:relative;width:640px;height:1136px;transform:scale(1.05625);transform-origin:0 0;font-family:"Open Sans",Arial,sans-serif;color:var(--white);overflow:hidden;background:var(--white);}
.app-header{position:absolute;left:0;top:0;width:640px;height:128px;background:var(--header-blue);}
.status-bar{position:absolute;left:0;top:0;width:640px;height:40px;font-size:22px;}
.status-bar .carrier{position:absolute;left:8px;top:6px;letter-spacing:0.5px;}
.status-bar .time{position:absolute;left:0;right:0;top:5px;text-align:center;font-weight:600;}
.status-bar .battery{position:absolute;right:10px;top:6px;display:flex;align-items:center;gap:6px;}
.menu-button{position:absolute;left:33px;top:70px;}
.search-field{position:absolute;left:93px;top:56px;width:513px;height:60px;background:var(--field-blue);}
.search-field .placeholder{position:absolute;left:0;width:434px;top:12px;text-align:center;font-style:italic;font-size:28px;}
.go-button{position:absolute;right:6px;top:10px;width:81px;height:40px;border-radius:6px;background:linear-gradient(#55d23c,#2ea81f);font-size:21px;text-align:center;line-height:40px;}
.swatch{position:absolute;width:88px;height:88px;border-radius:50%;display:flex;align-items:center;justify-content:center;}
.purple{background:linear-gradient(150deg,#a47ee8,#7a53de);}
.orange{background:linear-gradient(150deg,#f0903e,#ec5036);}
.sky{background:linear-gradient(150deg,#6cc3ef,#3fa8ea);}
.green{background:linear-gradient(150deg,#55cf3f,#23a823);}
.yellow{background:linear-gradient(150deg,#fcd23d,#f7b512);}
.grey{background:linear-gradient(150deg,#9e9e9e,#5f5f5f);}
.stop{position:absolute;left:32px;width:576px;height:90px;border-radius:6px;background:var(--item-blue);overflow:hidden;}
.stop .code{position:absolute;left:0;top:0;width:94px;height:90px;background:var(--code-blue);font-size:22px;line-height:90px;text-align:center;}
.stop .pin{position:absolute;left:110px;top:22px;}
.stop .name{position:absolute;left:138px;top:14px;font-size:29px;line-height:34px;white-space:nowrap;}
.stop .street{position:absolute;left:137px;top:52px;font-size:21px;line-height:26px;}
.stop .edit{position:absolute;left:470px;top:26px;}
.stop .star{position:absolute;left:515px;top:24px;}
.confirm{position:absolute;left:519px;top:902px;width:70px;height:70px;border-radius:50%;background:var(--check-green);display:flex;align-items:center;justify-content:center;box-shadow:0 2px 4px rgba(0,0,0,0.25);}
.ad-bar{position:absolute;left:0;top:1048px;width:640px;height:88px;background:var(--ad-dark);}
.ad-banner{position:absolute;left:36px;top:0;width:568px;height:88px;background:linear-gradient(90deg,#8c5a16,#c48a2a 55%,#d6a23a 75%,#9a6a1c);}
.ad-banner .label{position:absolute;left:22px;top:6px;font-size:33px;line-height:38px;}
.ad-banner .sponsor{position:absolute;left:290px;top:22px;display:flex;align-items:center;gap:12px;font-size:34px;}
.ad-banner .sponsor .mark{width:40px;height:40px;background:var(--white);}
.ad-banner .sponsor small{font-size:15px;align-self:flex-end;margin-bottom:6px;}
.ad-info{position:absolute;left:6px;bottom:6px;width:20px;height:20px;border-radius:50%;border:1.5px solid #bbb;color:#bbb;font-size:14px;line-height:20px;text-align:center;}
</style>
</head>
<body>
<div class="screen">
  <header class="app-header">
    <div class="status-bar">
      <span class="carrier">●●●○○ NORA</span>
      <span class="time">4:21 PM</span>
      <span class="battery">22%
        <svg width="44" height="20" viewBox="0 0 44 20"><rect x="1" y="1" width="38" height="18" rx="3" fill="none" stroke="#fff" stroke-width="2"/><rect x="4" y="4" width="9" height="12" fill="#fff"/><rect x="40" y="6" width="3" height="8" fill="#fff"/></svg>
      </span>
    </div>
    <svg class="menu-button" width="34" height="32" viewBox="0 0 34 32"><g stroke="#fff" stroke-width="3"><line x1="0" y1="2" x2="34" y2="2"/><line x1="0" y1="16" x2="34" y2="16"/><line x1="0" y1="30" x2="34" y2="30"/></g></svg>
    <div class="search-field">
      <span class="placeholder">Bus Stop Code</span>
      <span class="go-button">GO</span>
    </div>
  </header>

  <div class="swatch purple" style="left:29px;top:155px"></div>
  <div class="swatch orange" style="left:147px;top:155px"></div>
  <div class="swatch sky" style="left:268px;top:155px"><svg width="32" height="26" viewBox="0 0 32 26"><path d="M3 13l9 9L29 4" fill="none" stroke="#fff" stroke-width="4"/></svg></div>
  <div class="swatch green" style="left:385px;top:155px"></div>
  <div class="swatch yellow" style="left:503px;top:155px"></div>

  <div class="swatch purple" style="left:-55px;top:265px"></div>
  <div class="swatch orange" style="left:64px;top:265px"></div>
  <div class="swatch sky" style="left:185px;top:265px"></div>
  <div class="swatch green" style="left:302px;top:265px"><svg width="32" height="26" viewBox="0 0 32 26"><path d="M3 13l9 9L29 4" fill="none" stroke="#fff" stroke-width="4"/></svg></div>
  <div class="swatch yellow" style="left:420px;top:265px"></div>
  <div class="swatch grey" style="left:536px;top:265px"></div>

  <div class="stop" style="top:396px">
    <span class="code">09022</span>
    <svg class="pin" width="20" height="28" viewBox="0 0 20 28"><path d="M10 0a10 10 0 0 0-10 10c0 7 10 18 10 18s10-11 10-18A10 10 0 0 0 10 0zm0 14a4 4 0 1 1 0-8 4 4 0 0 1 0 8z" fill="#fff"/></svg>
    <span class="name">Opp Orchard stn</span>
    <span class="street">orchard boulevard</span>
    <svg class="edit" width="32" height="32" viewBox="0 0 32 32"><path d="M22 4H3v25h25V12" fill="none" stroke="#fff" stroke-width="3"/><path d="M12 22l1-6L27 2l5 5-14 14z" fill="#fff"/></svg>
    <svg class="star" width="40" height="38" viewBox="0 0 40 38"><path d="M20 0l6 13 14 1.5-10.5 9.5 3 14L20 31 7.5 38l3-14L0 14.5 14 13z" fill="var(--star)"/></svg>
  </div>

  <div class="stop" style="top:510px">
    <span class="code">10079</span>
    <svg class="pin" width="20" height="28" viewBox="0 0 20 28"><path d="M10 0a10 10 0 0 0-10 10c0 7 10 18 10 18s10-11 10-18A10 10 0 0 0 10 0zm0 14a4 4 0 1 1 0-8 4 4 0 0 1 0 8z" fill="#fff"/></svg>
    <span class="name">Blk 201</span>
    <span class="street">jln bt merah</span>
    <svg class="edit" width="32" height="32" viewBox="0 0 32 32"><path d="M22 4H3v25h25V12" fill="none" stroke="#fff" stroke-width="3"/><path d="M12 22l1-6L27 2l5 5-14 14z" fill="#fff"/></svg>
    <svg class="star" width="40" height="38" viewBox="0 0 40 38"><path d="M20 0l6 13 14 1.5-10.5 9.5 3 14L20 31 7.5 38l3-14L0 14.5 14 13z" fill="var(--star)"/></svg>
  </div>

  <div class="stop" style="top:627px">
    <span class="code">18141</span>
    <svg class="pin" width="20" height="28" viewBox="0 0 20 28"><path d="M10 0a10 10 0 0 0-10 10c0 7 10 18 10 18s10-11 10-18A10 10 0 0 0 10 0zm0 14a4 4 0 1 1 0-8 4 4 0 0 1 0 8z" fill="#fff"/></svg>
    <span class="name">Aft anglo-chinese jc</span>
    <span class="street">north bouna vista rd</span>
    <svg class="edit" width="32" height="32" viewBox="0 0 32 32"><path d="M22 4H3v25h25V12" fill="none" stroke="#fff" stroke-width="3"/><path d="M12 22l1-6L27 2l5 5-14 14z" fill="#fff"/></svg>
    <svg class="star" width="40" height="38" viewBox="0 0 40 38"><path d="M20 0l6 13 14 1.5-10.5 9.5 3 14L20 31 7.5 38l3-14L0 14.5 14 13z" fill="var(--star)"/></svg>
  </div>

  <div class="stop" style="top:742px">
    <span class="code">66081</span>
    <svg class="pin" width="20" height="28" viewBox="0 0 20 28"><path d="M10 0a10 10 0 0 0-10 10c0 7 10 18 10 18s10-11 10-18A10 10 0 0 0 10 0zm0 14a4 4 0 1 1 0-8 4 4 0 0 1 0 8z" fill="#fff"/></svg>
    <span class="name">Opp s’pore po..</span>
    <span class="street">bladdell rd</span>
    <svg class="edit" width="32" height="32" viewBox="0 0 32 32"><path d="M22 4H3v25h25V12" fill="none" stroke="#fff" stroke-width="3"/><path d="M12 22l1-6L27 2l5 5-14 14z" fill="#fff"/></svg>
    <svg class="star" width="40" height="38" viewBox="0 0 40 38"><path d="M20 0l6 13 14 1.5-10.5 9.5 3 14L20 31 7.5 38l3-14L0 14.5 14 13z" fill="var(--star)"/></svg>
  </div>

  <div class="stop" style="top:856px">
    <span class="code">08031</span>
    <svg class="pin" width="20" height="28" viewBox="0 0 20 28"><path d="M10 0a10 10 0 0 0-10 10c0 7 10 18 10 18s10-11 10-18A10 10 0 0 0 10 0zm0 14a4 4 0 1 1 0-8 4 4 0 0 1 0 8z" fill="#fff"/></svg>
    <span class="name">Dhob...</span>
    <span class="street">penang rd</span>
    <svg class="edit" width="32" height="32" viewBox="0 0 32 32"><path d="M22 4H3v25h25V12" fill="none" stroke="#fff" stroke-width="3"/><path d="M12 22l1-6L27 2l5 5-14 14z" fill="#fff"/></svg>
    <svg class="star" width="40" height="38" viewBox="0 0 40 38"><path d="M20 0l6 13 14 1.5-10.5 9.5 3 14L20 31 7.5 38l3-14L0 14.5 14 13z" fill="var(--star)"/></svg>
  </div>

  <div class="confirm"><svg width="32" height="26" viewBox="0 0 32 26"><path d="M3 13l9 9L29 4" fill="none" stroke="#fff" stroke-width="4"/></svg></div>

  <footer class="ad-bar">
    <div class="ad-banner" role="img" aria-label="Test advertising banner with warm golden background">
      <span class="label">320x50<br>Test Banner</span>
      <span class="sponsor"><span class="mark"></span>Adlume <small>by Trivex</small></span>
    </div>
    <span class="ad-info">i</span>
  </footer>
</div>
</body>
</html>
```